Paul Denton Sausage Label Design

Halvern Fields Corporation is seeking to create a new brand of fresh 100% Canadian pork sausage. This label will be a paper band that slips on and off foam trays. The front facing side will be 5 inches wide by 3.5 inches high. The following is some information about our brand.
Target market:
1. Working Moms
2. Stay at home moms
3. Barbeque enthusiast
Brand personality
1. Old school values – We are a family run company who believes in an honest days work
2. Modern day sensibility – We believe in being nimble and open to new ideas
3. Energetic and optimistic – We are passionate about our business and product
4. Relaxed sense of humor – We believe that it is possible to work hard and have fun
Positioning Statements:
Our sausage is the easy choice for adding flavour to your real- life family meals, that’s because:
1. It is 100% fresh Canadian product with no fillers or preservatives
2. It is a great tasting recipe with simple, natural ingredients
3. It is brought to you with good humor and integrity by a multi- generational family owned business
We are looking for a creative designer to make our ideas come to life. There are three types of designs we would like to see:
1. Rustic – a rustic, barbequing, old farm, country feel – without feeling too old
2. Modern & Simple – Very simple clean face with clean text
3. Family friendly – a label that would appeal to the everyday family with photos of the finished product
This brand does not have a name yet, please use the name “Paul Denton “as a place holder. Please keep in mind the information provided about our brand when developing the label. Attached are pictures of some ideas we like. Please do not copy these ideas too closely, we are looking to differentiate ourselves in the market. Samples are to provide some guidance of our preferences.
Target Market(s)
1. Working Moms
2. Stay at home moms
3. Barbeque enthusiast
Colors
Designer to choose colors to be used in the design.

```html
<!DOCTYPE html>
<html lang="en">
<head>
<meta charset="utf-8">
<title>Paul Denton Sausage Labels</title>
<link href="https://fonts.googleapis.com/css2?family=Arvo:wght@400;700&family=Yesteryear&display=swap" rel="stylesheet">
<style>
  :root {
    --page: #efe9d6;
    --cream: #fdfbee;
    --green: #b5c843;
    --green-ink: #1f4a12;
    --red: #c93f45;
    --red-ink: #3a1a0c;
    --blue: #3a6fc8;
    --blue-ink: #1a1459;
    --orange: #d9822b;
    --orange-ink: #3a2b10;
  }
  * { box-sizing: border-box; margin: 0; padding: 0; }
  html, body { width: 1200px; height: 1200px; overflow: hidden; background: var(--page); }
  .sheet {
    position: relative; width: 1200px; height: 1200px;
    display: grid; grid-template-columns: 560px 560px; grid-template-rows: 392px 392px;
    gap: 28px; padding: 194px 26px;
  }
  .label {
    position: relative; width: 560px; height: 392px;
    background: var(--bg); color: var(--cream);
    font-family: "Arvo", Georgia, serif; font-weight: 700;
    box-shadow: 0 4px 12px rgba(0,0,0,0.15);
    overflow: hidden;
  }
  .label--green { --bg: var(--green); --ink: var(--green-ink); }
  .label--red { --bg: var(--red); --ink: var(--red-ink); }
  .label--blue { --bg: var(--blue); --ink: var(--blue-ink); }
  .label--orange { --bg: var(--orange); --ink: var(--orange-ink); }
  .label > * { position: absolute; }
  .rule { background: var(--cream); }
  .rule--h { height: 2px; }
  .rule--v { width: 2px; }
  .corp { left: 22px; top: 24px; font-size: 11.5px; letter-spacing: 0.02em; }
  .brand {
    left: 20px; top: 56px; font-size: 46px; line-height: 50px;
    text-shadow: 3px 3px 0 var(--ink);
  }
  .cuts-art {
    left: 278px; top: 22px; width: 262px; height: 158px;
    background: radial-gradient(ellipse 48% 40% at 50% 52%, var(--cream) 0 94%, transparent 96%);
  }
  .map-art {
    left: 22px; top: 212px; width: 100px; height: 78px;
    background: var(--cream); opacity: 0.95;
    border-radius: 30% 40% 20% 35% / 40% 30% 40% 30%;
  }
  .script { font-family: "Yesteryear", cursive; font-weight: 400; color: var(--cream); line-height: 1; }
  .origin { left: 118px; top: 208px; font-size: 17px; width: 80px; transform: rotate(-4deg); }
  .natural { left: 214px; top: 198px; font-size: 24px; }
  .flavour { left: 214px; top: 236px; font-size: 28px; color: var(--ink); }
  .kind { left: 222px; top: 272px; font-size: 13px; }
  .desc { left: 214px; top: 312px; font-size: 12.5px; line-height: 17px; }
  .count { left: 30px; top: 328px; font-size: 14px; }
  .weight { left: 82px; top: 318px; font-size: 16px; }
  .weight .mark { font-family: Georgia, serif; font-weight: 400; font-size: 20px; margin-left: 4px; }
  .storage { left: 82px; top: 345px; font-size: 6.8px; }
</style>
</head>
<body>
<main class="sheet">
  <article class="label label--green">
    <p class="corp">HALVERN FIELDS CORPORATION</p>
    <div class="rule rule--h" style="left:0;top:44px;width:258px"></div>
    <h1 class="brand">PAUL<br>DENTON</h1>
    <div class="rule rule--v" style="left:258px;top:0;height:190px"></div>
    <div class="cuts-art" role="img" aria-label="Illustrated pig with butcher cut diagram: ham, loin, shoulder, spare ribs, picnic ham, bacon"></div>
    <div class="rule rule--h" style="left:0;top:190px;width:560px"></div>
    <div class="map-art" role="img" aria-label="Map silhouette of Canada"></div>
    <p class="script origin">100% Canadian</p>
    <div class="rule rule--v" style="left:200px;top:196px;height:196px"></div>
    <p class="script natural">All Natural</p>
    <div class="rule rule--h" style="left:200px;top:230px;width:346px"></div>
    <h2 class="flavour">MUTTON &amp; MINT</h2>
    <p class="kind">PORK SAUSAGES</p>
    <div class="rule rule--h" style="left:200px;top:300px;width:346px"></div>
    <p class="desc">6 MATURE MUTTON SAUSAGE,<br>INFUSED WITH MINT.</p>
    <div class="rule rule--h" style="left:14px;top:304px;width:186px"></div>
    <p class="count">X6</p>
    <div class="rule rule--v" style="left:68px;top:304px;height:74px"></div>
    <p class="weight">400G<span class="mark">℮</span></p>
    <p class="storage">KEEP REFRIGERATED</p>
  </article>

  <article class="label label--red">
    <p class="corp">HALVERN FIELDS CORPORATION</p>
    <div class="rule rule--h" style="left:0;top:44px;width:258px"></div>
    <h1 class="brand">PAUL<br>DENTON</h1>
    <div class="rule rule--v" style="left:258px;top:0;height:190px"></div>
    <div class="cuts-art" role="img" aria-label="Illustrated pig with butcher cut diagram: ham, loin, shoulder, spare ribs, picnic ham, bacon"></div>
    <div class="rule rule--h" style="left:0;top:190px;width:560px"></div>
    <div class="map-art" role="img" aria-label="Map silhouette of Canada"></div>
    <p class="script origin">100% Canadian</p>
    <div class="rule rule--v" style="left:200px;top:196px;height:196px"></div>
    <p class="script natural">All Natural</p>
    <div class="rule rule--h" style="left:200px;top:230px;width:346px"></div>
    <h2 class="flavour">MUTTON &amp; MINT</h2>
    <p class="kind">PORK SAUSAGES</p>
    <div class="rule rule--h" style="left:200px;top:300px;width:346px"></div>
    <p class="desc">6 MATURE MUTTON SAUSAGE,<br>INFUSED WITH MINT.</p>
    <div class="rule rule--h" style="left:14px;top:304px;width:186px"></div>
    <p class="count">X6</p>
    <div class="rule rule--v" style="left:68px;top:304px;height:74px"></div>
    <p class="weight">400G<span class="mark">℮</span></p>
    <p class="storage">KEEP REFRIGERATED</p>
  </article>

  <article class="label label--blue">
    <p class="corp">HALVERN FIELDS CORPORATION</p>
    <div class="rule rule--h" style="left:0;top:44px;width:258px"></div>
    <h1 class="brand">PAUL<br>DENTON</h1>
    <div class="rule rule--v" style="left:258px;top:0;height:190px"></div>
    <div class="cuts-art" role="img" aria-label="Illustrated pig with butcher cut diagram: ham, loin, shoulder, spare ribs, picnic ham, bacon"></div>
    <div class="rule rule--h" style="left:0;top:190px;width:560px"></div>
    <div class="map-art" role="img" aria-label="Map silhouette of Canada"></div>
    <p class="script origin">100% Canadian</p>
    <div class="rule rule--v" style="left:200px;top:196px;height:196px"></div>
    <p class="script natural">All Natural</p>
    <div class="rule rule--h" style="left:200px;top:230px;width:346px"></div>
    <h2 class="flavour">MUTTON &amp; MINT</h2>
    <p class="kind">PORK SAUSAGES</p>
    <div class="rule rule--h" style="left:200px;top:300px;width:346px"></div>
    <p class="desc">6 MATURE MUTTON SAUSAGE,<br>INFUSED WITH MINT.</p>
    <div class="rule rule--h" style="left:14px;top:304px;width:186px"></div>
    <p class="count">X6</p>
    <div class="rule rule--v" style="left:68px;top:304px;height:74px"></div>
    <p class="weight">400G<span class="mark">℮</span></p>
    <p class="storage">KEEP REFRIGERATED</p>
  </article>

  <article class="label label--orange">
    <p class="corp">HALVERN FIELDS CORPORATION</p>
    <div class="rule rule--h" style="left:0;top:44px;width:258px"></div>
    <h1 class="brand">PAUL<br>DENTON</h1>
    <div class="rule rule--v" style="left:258px;top:0;height:190px"></div>
    <div class="cuts-art" role="img" aria-label="Illustrated pig with butcher cut diagram: ham, loin, shoulder, spare ribs, picnic ham, bacon"></div>
    <div class="rule rule--h" style="left:0;top:190px;width:560px"></div>
    <div class="map-art" role="img" aria-label="Map silhouette of Canada"></div>
    <p class="script origin">100% Canadian</p>
    <div class="rule rule--v" style="left:200px;top:196px;height:196px"></div>
    <p class="script natural">All Natural</p>
    <div class="rule rule--h" style="left:200px;top:230px;width:346px"></div>
    <h2 class="flavour">MUTTON &amp; MINT</h2>
    <p class="kind">PORK SAUSAGES</p>
    <div class="rule rule--h" style="left:200px;top:300px;width:346px"></div>
    <p class="desc">6 MATURE MUTTON SAUSAGE,<br>INFUSED WITH MINT.</p>
    <div class="rule rule--h" style="left:14px;top:304px;width:186px"></div>
    <p class="count">X6</p>
    <div class="rule rule--v" style="left:68px;top:304px;height:74px"></div>
    <p class="weight">400G<span class="mark">℮</span></p>
    <p class="storage">KEEP REFRIGERATED</p>
  </article>
</main>
</body>
</html>
```